Website: BrightHarbor Business Consultants, Lanwan SEZ, China

Our client is a business consultancy firm and will be the first to set up in the Lanwan Shenzhen-Hong Kong Modern Service Industry Cooperation Zone, China So we need a corporate website concept that engages service, finance and technology sector companies. The company can provide all the necessary services needed to set up shop in Lanwan. They are looking for a modern, international, reliable and strong image.

Here are some websites for reference prupose:

http://www.vornelpax.com/ (we like the dynamic banner and clear, clean layout of this website)

http://www.quilbrenadvisory.com/ (we like the background city image, use of light font, hover over menu functions and color scheme - purple and grey)

http://www.dovu.com/ (we like the simplicity of this website, clear lines and we like the dynamic banner)
Updates

Hello, We are currently undecided between three logo designs.  All three have been uploaded to the design brief so that you can use them as reference for the website design. Thx

Also please take note of the addition menu selection 'About Lanwan'. Thx

Hello all Designers, First of all we want thank you for participating in our website competition, the calibre of design was high and we appreciated the expedience. Our company is Lumen Harvest Web Design and Internet Marketing based in Shenzhen, China. We anticipate rapid growth in the Chinese domestic market as the country shifts in to a service sector economy. We hope to continue building reliable working relationships with you based on idea sharing and constructive feedback. Once again, Thankyou, LH Team

Target Market(s)

International finance and technology companies looking to set up in Lanwan Special Economic Zone, China

Industry/Entity Type

Finance

Requirements
Must have
• Initial design for home page and in later selection stages a secondary page will be required.

The design should be for PSD concepts only no code!

Menu bar, Photo banner -
A. Photo banner and text overlay,
B.Photo Banner and text description to left or right.

Social Connect icons, Site search bar (top right), Logo space (top left).

Menu bar at top with Home, About Us, About Lanwan, Services, Portfolio, Partners, Our Team Contact Us.

Standard 3-4 box layout - Banner at top and 2-3 boxes under banner.

Colour scheme- A. Purple and Blue, must have light background/body
B. Shades of white, black and grey.

Simple, clear, clean, sharp.

```html
<!DOCTYPE html>
<html lang="en">
<head>
<meta charset="utf-8">
<title>BrightHarbor Business Consultants</title>
<link href="https://fonts.googleapis.com/css2?family=Open+Sans:wght@300;400;600&family=Source+Sans+3:wght@300;400&family=Crimson+Text:wght@400&display=swap" rel="stylesheet">
<style>
:root{
  --blue:#1a9fd3;
  --pink:#d0149e;
  --ink:#333;
  --grey-text:#8a8a8a;
  --footer:#222;
  --footer-text:#e6e6e6;
  --line:#d9d9d9;
}
*{margin:0;padding:0;box-sizing:border-box}
html,body{width:1200px;height:1078px;overflow:hidden}
body{position:relative;background:#fff;font-family:"Open Sans",Arial,sans-serif;color:var(--ink)}
.abs{position:absolute}
.city-backdrop{left:0;top:0;width:1200px;height:596px;background:linear-gradient(90deg,#6a6f78 0%,#1d2128 10%,#0d1016 14%,#1b2a45 86%,#3b5a86 92%,#8ea3bd 100%)}
.page{left:166px;top:8px;width:862px;height:152px;background:#fff}
.brand{left:24px;top:95px;font-size:26px;font-weight:600;color:#222;letter-spacing:.5px}
.phone{left:635px;top:35px;display:flex;align-items:center;gap:8px;color:var(--blue);font-size:15px}
.social{display:flex;gap:6px}
.social span{display:block;width:26px;height:26px;border-radius:50%;background:#d5d8dd;box-shadow:inset 0 0 0 1px #c2c6cc}
.header-social{left:758px;top:36px}
.search{left:650px;top:85px;width:198px;height:21px;border:1px solid #ccc;border-radius:3px;font-size:10px;color:#888;padding:3px 14px;display:flex;justify-content:space-between}
.search svg{margin-right:-10px}
.nav{left:294px;top:120px;display:flex;font-size:11px;font-weight:600;color:var(--blue)}
.nav a{text-decoration:none;color:inherit;margin-right:28px;line-height:20px}
.nav a.active{background:var(--pink);color:#fff;border-radius:4px;padding:0 8px;margin-right:20px}
.banner{left:166px;top:160px;width:862px;height:373px;background:linear-gradient(100deg,#ececec 0%,#dcdcdc 35%,#6d6f74 60%,#303237 80%,#a9abaf 100%)}
.banner-band{left:166px;top:405px;width:862px;height:128px;background:rgba(90,90,90,.65)}
.banner-title{left:201px;top:460px;font-family:"Crimson Text",Georgia,serif;font-size:34px;font-weight:400;color:#fff;letter-spacing:.3px;white-space:nowrap}
.rule{left:166px;top:545px;width:862px;height:1px;background:#444}
.tab{top:555px;width:281px;height:42px;color:#fff;font-family:"Crimson Text",Georgia,serif;font-size:22px;text-align:center;line-height:42px;letter-spacing:-.3px}
.tab.blue{background:var(--blue)}
.tab.pink{background:var(--pink)}
.card{top:612px;width:281px;height:261px;border:1px solid var(--line);background:radial-gradient(ellipse at 50% 75%,#fff 0%,#fafafa 50%,#eee 100%)}
.card p.copy-text{position:absolute;left:21px;top:20px;width:256px;font-family:"Source Sans 3",Arial,sans-serif;font-size:11.3px;font-weight:400;line-height:18px;color:var(--grey-text)}
.readmore{position:absolute;left:183px;top:213px;width:81px;height:19px;border-radius:10px;background:#555;color:#fff;font-size:10px;text-align:center;line-height:19px}
.news{position:absolute;left:9px;width:261px;height:64px;border-bottom:1px dotted #c9c9c9}
.date{position:absolute;left:0;top:0;width:34px;height:35px;background:var(--blue);color:#fff;font-size:12px;line-height:13px;text-align:center;padding-top:4px}
.date small{font-size:10px;display:block}
.news h4{position:absolute;left:44px;top:0;font-size:12px;font-weight:600;color:#888;text-decoration:underline}
.news p{position:absolute;left:44px;top:18px;width:215px;font-size:8.5px;line-height:11px;color:#888;font-weight:400}
.footer-top-line{left:0;top:884px;width:1200px;height:1px;background:#ccc}
.footer{left:0;top:888px;width:1200px;height:190px;background:var(--footer);color:var(--footer-text)}
.footer h3{position:absolute;top:20px;font-size:15px;font-weight:400}
.contact{position:absolute;left:171px;top:52px;font-size:12px;line-height:20.7px;font-weight:400}
.divider{position:absolute;top:26px;width:1px;height:108px;background:#3a3a3a}
.member{position:absolute;top:52px;width:52px;text-align:center}
.member div{width:52px;height:52px;border-radius:50%;background:radial-gradient(circle,#a58a76,#5e4a3e);border:2px solid #ddd}
.member span{display:block;margin-top:12px;font-size:11px;color:#777}
.blog{position:absolute;left:657px;top:52px;font-size:12px;line-height:20.7px;font-weight:400}
.blog a{display:block;color:var(--footer-text)}
.footer-social{position:absolute;left:902px;top:52px}
.footer-brand{position:absolute;left:902px;top:98px;font-size:19px;font-weight:600;color:#999}
.copy-line{position:absolute;left:0;top:154px;width:1200px;height:1px;background:#303030}
.copy{position:absolute;left:171px;top:164px;font-size:11px;color:#fff}
</style>
</head>
<body>
<div class="abs city-backdrop" role="img" aria-label="Blurred city skyline with office buildings and clouds"></div>

<header class="abs page">
  <div class="abs brand">BrightHarbor</div>
  <div class="abs phone">
    <svg width="28" height="28" viewBox="0 0 28 28"><circle cx="14" cy="14" r="12.5" fill="none" stroke="#d0149e" stroke-width="2"/><path d="M10 8c1-1 2 0 2.5 1.5s.5 2-.5 2.5c.5 2 2 3.5 4 4.5.5-1 1.5-1 2.5-.5s2 1.5 1 2.5c-1.5 1.5-4 1-6.5-1.5S8.5 9.5 10 8z" fill="#d0149e"/></svg>
    0800-67890
  </div>
  <div class="abs social header-social"><span></span><span></span><span></span></div>
  <div class="abs search">Enter Key word
    <svg width="14" height="14" viewBox="0 0 14 14"><circle cx="6" cy="6" r="4" fill="none" stroke="#d0149e" stroke-width="1.6"/><path d="M9 9l3.5 3.5" stroke="#d0149e" stroke-width="2"/></svg>
  </div>
  <nav class="abs nav">
    <a class="active" href="#">Home</a><a href="#">About Lanwan</a><a href="#">Services</a><a href="#">Portfolio</a><a href="#">Partners</a><a href="#">Our Team</a><a href="#">Contact Us</a>
  </nav>
</header>

<div class="abs banner" role="img" aria-label="Businessman in a grey suit holding a puzzle piece marked success"></div>
<div class="abs banner-band"></div>
<h1 class="abs banner-title">GROW UP YOUR BUSINESS WITH BRIGHT HARBOR</h1>
<div class="abs rule"></div>

<div class="abs tab blue" style="left:166px">WHO WE ARE</div>
<div class="abs tab pink" style="left:456px">WHAT WE DO</div>
<div class="abs tab blue" style="left:747px">NEWS UP DATE</div>

<section class="abs card" style="left:166px">
  <p class="copy-text">Barite is a mineral composed of barium sulfate, BaSO4. It is usually colorless or milky white, but can be almost any color, depending on the impurities trapped in the crystals during their formation. Barite is relatively soft, measuring 3-3.5 on Moh's scale of hardness. It is unusually heavy for a non-metallic mineral. The high density is responsible for its value in many applications. Barite is chemically inert and insoluble.</p>
  <div class="readmore">READMORE</div>
</section>
<section class="abs card" style="left:456px">
  <p class="copy-text" style="left:10px">Barite is a mineral composed of barium sulfate, BaSO4. It is usually colorless or milky white, but can be almost any color, depending on the impurities trapped in the crystals during their formation. Barite is relatively soft, measuring 3-3.5 on Moh's scale of hardness. It is unusually heavy for a non-metallic mineral. The high density is responsible for its value in many applications. Barite is chemically inert and insoluble.</p>
  <div class="readmore" style="left:182px">READMORE</div>
</section>
<section class="abs card" style="left:747px">
  <div class="news" style="top:20px"><div class="date">24<small>JAN</small></div><h4>Lorem ipsum dolor sit amet</h4><p>sed diam nonummy nibh euismod tincidunt ut laoreet dolore magna....</p></div>
  <div class="news" style="top:84px"><div class="date">24<small>JAN</small></div><h4>Lorem ipsum dolor sit amet</h4><p>sed diam nonummy nibh euismod tincidunt ut laoreet dolore magna...</p></div>
  <div class="news" style="top:147px;border:none"><div class="date">23<small>JAN</small></div><h4>Lorem ipsum dolor sit amet</h4><p style="width:190px">sed diam nonummy nibh euismod tincidunt ut laoreet dolore magna...</p></div>
  <div class="readmore" style="left:182px">READMORE</div>
</section>

<div class="abs footer-top-line"></div>
<footer class="abs footer">
  <h3 style="left:171px">Contact Us</h3>
  <div class="contact">TEL: 000-200-2001<br>Fax: 000-200-2002<br>218 Harbor View Road Suite 604<br>Lakemont, TX 1234</div>
  <div class="divider" style="left:387px"></div>
  <h3 style="left:419px">Our Team</h3>
  <div class="member" style="left:419px"><div role="img" aria-label="Team member portrait"></div><span>Daniel</span></div>
  <div class="member" style="left:482px"><div role="img" aria-label="Team member portrait"></div><span>Marta</span></div>
  <div class="member" style="left:542px"><div role="img" aria-label="Team member portrait"></div><span>Oskar</span></div>
  <div class="divider" style="left:630px"></div>
  <h3 style="left:667px">Blog</h3>
  <div class="blog"><a href="#">Lorem ipsum dolor sit amet</a><a href="#">Lorem ipsum dolor sit amet</a><a href="#">Lorem ipsum dolor sit amet</a><a href="#">Lorem ipsum dolor sit amet</a></div>
  <div class="divider" style="left:830px"></div>
  <h3 style="left:905px">Follow Us</h3>
  <div class="social footer-social"><span></span><span></span><span></span></div>
  <div class="footer-brand">BrightHarbor</div>
  <div class="copy-line"></div>
  <div class="copy">©2013 &nbsp;brightharbor-example.com. All rights reserved.</div>
</footer>
</body>
</html>
```